Modern Business Card

Modern professional business card with more than just logo and demographic info. Something memorable.

We are a trendy/modern chiropractic group with an emphasis on neurology, hence the minimalist-type brain logo. We want to convey that modern and technical aspect with professionalism and the elite nature of our practice environment.

```html
<!DOCTYPE html>
<html lang="en">
<head>
<meta charset="utf-8">
<title>Meridian Spine – Business Card</title>
<link rel="stylesheet" href="https://fonts.googleapis.com/css2?family=Noto+Serif:wght@700&family=Open+Sans:wght@400;600&display=swap">
<style>
  :root {
    --brand-blue: #4680c2;
    --ink-dark: #3d3d3f;
    --ink-text: #4a4a4c;
    --paper: #ffffff;
    --backdrop: #e6e7ea;
    --card-w: 680px;
    --card-h: 388px;
  }
  * { box-sizing: border-box; margin: 0; padding: 0; }
  html, body {
    width: 1200px; height: 901px; overflow: hidden;
    background: var(--backdrop);
  }
  .canvas {
    width: 1200px; height: 901px;
    display: flex; flex-direction: column; align-items: center; justify-content: center;
    gap: 40px;
  }
  .card {
    position: relative;
    width: var(--card-w); height: var(--card-h);
    box-shadow: 0 10px 24px rgba(0,0,0,.18);
    overflow: hidden;
  }
  .card--front {
    background: var(--brand-blue);
    display: flex; align-items: center; justify-content: center;
  }
  .wordmark {
    display: flex; align-items: center; gap: 18px;
    font-family: "Noto Serif", Georgia, serif; font-weight: 700;
    text-transform: uppercase; line-height: 1;
  }
  .wordmark__square { width: 46px; height: 46px; }
  .wordmark--front { color: var(--paper); font-size: 50px; letter-spacing: 3px; }
  .wordmark--front .wordmark__square { background: var(--paper); }
  .wordmark--back { color: var(--ink-dark); font-size: 26px; letter-spacing: 1.5px; gap: 12px; }
  .wordmark--back .wordmark__square { width: 26px; height: 26px; background: var(--brand-blue); }

  .card--back { background: var(--paper); }
  .card--back .wordmark { position: absolute; top: 82px; right: 48px; }

  .person { position: absolute; left: 56px; top: 150px; }
  .person__name {
    font-family: "Noto Serif", Georgia, serif; font-weight: 700;
    color: var(--brand-blue); font-size: 25px; letter-spacing: .5px; text-transform: uppercase;
  }
  .person__role {
    font-family: "Open Sans", Arial, sans-serif; color: var(--ink-text);
    font-size: 16px; margin-top: 2px;
  }
  .contacts {
    position: absolute; left: 72px; top: 236px; list-style: none;
    font-family: "Open Sans", Arial, sans-serif; color: var(--ink-text); font-size: 16px;
  }
  .contacts li { display: flex; align-items: center; gap: 8px; line-height: 22px; }
  .contacts svg { width: 12px; height: 12px; fill: var(--brand-blue); flex: none; }

  .bands { position: absolute; left: 0; bottom: 0; width: 100%; height: 100px; }
  .band-text {
    position: absolute; font-family: "Open Sans", Arial, sans-serif; color: var(--paper); font-size: 15px;
  }
  .band-text--address { left: 36px; bottom: 36px; }
  .band-text--web { right: 22px; bottom: 50px; display: flex; align-items: center; gap: 8px; }
  .band-text--web svg { width: 12px; height: 12px; }
</style>
</head>
<body>
<main class="canvas">
  <section class="card card--front" aria-label="Card front">
    <div class="wordmark wordmark--front">
      <span class="wordmark__square" aria-hidden="true"></span>
      <span>Meridian Spine</span>
    </div>
  </section>

  <section class="card card--back" aria-label="Card back">
    <div class="wordmark wordmark--back">
      <span class="wordmark__square" aria-hidden="true"></span>
      <span>Meridian Spine</span>
    </div>

    <div class="person">
      <h1 class="person__name">Daniel Marsh</h1>
      <p class="person__role">Senior Partner</p>
    </div>

    <ul class="contacts">
      <li>
        <svg viewBox="0 0 12 12" aria-hidden="true"><path d="M2.5 1 4.5 3.2 3.4 4.6c.7 1.6 2.1 3 3.7 3.7L8.5 7l2.2 2-1.3 1.8C5.2 10.5 1.5 6.8 1 2.4z"/></svg>
        +120 5410 2871
      </li>
      <li>
        <svg viewBox="0 0 12 12" aria-hidden="true"><path d="M3.5 .5h5a1 1 0 0 1 1 1v9a1 1 0 0 1-1 1h-5a1 1 0 0 1-1-1v-9a1 1 0 0 1 1-1zm.3 1.3v7.4h4.4V1.8zM6 9.8a.6.6 0 1 0 0 1.2.6.6 0 0 0 0-1.2z"/></svg>
        +965 8617 4402
      </li>
      <li>
        <svg viewBox="0 0 12 12" aria-hidden="true"><path d="M.5 2.5h11v7h-11zm1 .8L6 6.6l4.5-3.3z"/></svg>
        hello@meridianspine.com
      </li>
    </ul>

    <svg class="bands" viewBox="0 0 680 100" preserveAspectRatio="none" aria-hidden="true">
      <polygon points="0,38 452,38 438,80 0,80" fill="var(--ink-dark)"/>
      <polygon points="466,18 680,18 680,62 450,62" fill="var(--brand-blue)"/>
    </svg>
    <p class="band-text band-text--address">12 Ridgeway Lane Northvale Pretoria, 0181</p>
    <p class="band-text band-text--web">
      www.meridianspine.com
      <svg viewBox="0 0 12 12" aria-hidden="true" fill="none" stroke="#fff" stroke-width="1"><circle cx="6" cy="6" r="5"/><ellipse cx="6" cy="6" rx="2.2" ry="5"/><path d="M1 6h10M2 3.5h8M2 8.5h8"/></svg>
    </p>
  </section>
</main>
</body>
</html>
```